Veltrano.co - Polar Expeditions Specialists

We need a modern, visually striking business card for Veltrano.co, a company specialized in selling expedition cruises to the most remote regions on Earth, with a focus on the Arctic and Antarctica. The design should instantly communicate that the cardholder is an expert in polar travel. Use clean, premium aesthetics with cool tones like icy blue and white, possibly incorporating polar imagery (ice, glaciers, penguins, etc.)

Attached the logo

Contact Information for Business Card

Feels high-end and trustworthy.. Visually memorable — encourages people to keep it

Colors
0054AA
0677BA
7BADD7
CADEEF
E8F1F8

Requirements
Must have
• ice, glaciers, penguins, montains
Nice to have
• modern, transparente,

```html
<!DOCTYPE html>
<html lang="en">
<head>
<meta charset="utf-8">
<title>Veltrano.co – Business Card</title>
<link href="https://fonts.googleapis.com/css2?family=Poppins:wght@400;500;700;800&display=swap" rel="stylesheet">
<style>
  :root {
    --page-bg: #e4e7ec;
    --card-white: #ffffff;
    --card-navy: #0b0c2b;
    --brand-blue: #3577c0;
    --ink: #1d1d24;
    --white: #ffffff;
  }
  * { box-sizing: border-box; margin: 0; padding: 0; }
  html, body { width: 1200px; height: 1195px; overflow: hidden; }
  body {
    background: var(--page-bg);
    font-family: "Poppins", sans-serif;
    display: flex;
    align-items: center;
    justify-content: center;
    gap: 70px;
  }
  .card {
    width: 440px;
    height: 720px;
    border-radius: 34px;
    position: relative;
    box-shadow: 0 10px 30px rgba(0,0,0,0.12);
  }

  /* Front */
  .card-front {
    background: var(--card-white);
    display: flex;
    flex-direction: column;
    align-items: center;
    text-align: center;
    padding-top: 96px;
  }
  .brand-mark {
    width: 84px; height: 84px;
    border-radius: 50%;
    background: var(--brand-blue);
    margin-bottom: 14px;
  }
  .brand-name {
    font-weight: 800;
    font-size: 54px;
    line-height: 1;
    color: var(--brand-blue);
    letter-spacing: -0.5px;
  }
  .brand-tagline {
    font-weight: 700;
    font-size: 17px;
    color: var(--brand-blue);
    margin-top: 6px;
  }
  .holder-name {
    margin-top: 100px;
    font-weight: 700;
    font-size: 25px;
    color: var(--brand-blue);
  }
  .holder-role {
    font-size: 14px;
    color: var(--ink);
    margin-top: 2px;
  }
  .contact-icons {
    display: flex;
    align-items: center;
    gap: 8px;
    margin-top: 22px;
  }
  .contact-icons .rule {
    width: 30px; height: 1.5px;
    background: var(--brand-blue);
  }
  .contact-icons .icon {
    width: 22px; height: 22px;
    border-radius: 6px;
    background: var(--brand-blue);
    display: flex; align-items: center; justify-content: center;
  }
  .contact-list {
    margin-top: 14px;
    font-size: 15.5px;
    line-height: 1.45;
    color: var(--ink);
  }
  .divider {
    width: 70px; height: 1.5px;
    background: var(--brand-blue);
    margin: 16px 0 14px;
  }
  .address {
    font-size: 15.5px;
    line-height: 1.45;
    color: var(--ink);
  }

  /* Back */
  .card-back {
    background: var(--card-navy);
    overflow: hidden;
  }
  .back-lockup {
    position: absolute;
    left: 50%; top: 50%;
    transform: translate(-50%, -50%) rotate(-90deg);
    display: flex;
    align-items: center;
    gap: 26px;
    white-space: nowrap;
  }
  .back-mark {
    width: 120px; height: 120px;
    border-radius: 50%;
    background: var(--white);
  }
  .back-text .brand-name { color: var(--white); font-size: 70px; }
  .back-text .brand-tagline { color: var(--white); font-size: 23px; margin-top: 4px; }
</style>
</head>
<body>
  <article class="card card-front">
    <div class="brand-mark"></div>
    <div class="brand-name">Veltrano.co</div>
    <div class="brand-tagline">Polar Expeditions Specialists</div>

    <div class="holder-name">Marlo Quenby</div>
    <div class="holder-role">CEO &amp; Founder</div>

    <div class="contact-icons">
      <span class="rule"></span>
      <span class="icon">
        <svg width="13" height="13" viewBox="0 0 24 24" fill="#fff"><path d="M6.6 10.8a15 15 0 0 0 6.6 6.6l2.2-2.2a1 1 0 0 1 1-.25 11.4 11.4 0 0 0 3.6.57 1 1 0 0 1 1 1V20a1 1 0 0 1-1 1A17 17 0 0 1 3 4a1 1 0 0 1 1-1h3.5a1 1 0 0 1 1 1c0 1.25.2 2.45.57 3.57a1 1 0 0 1-.25 1z"/></svg>
      </span>
      <span class="icon">
        <svg width="13" height="13" viewBox="0 0 24 24" fill="none" stroke="#fff" stroke-width="2.2"><rect x="3" y="5" width="18" height="14" rx="2"/><path d="M3 7l9 6 9-6"/></svg>
      </span>
      <span class="icon">
        <svg width="13" height="13" viewBox="0 0 24 24" fill="none" stroke="#fff" stroke-width="2"><circle cx="12" cy="12" r="9"/><path d="M3 12h18M12 3c3 3.5 3 14.5 0 18M12 3c-3 3.5-3 14.5 0 18"/></svg>
      </span>
      <span class="rule"></span>
    </div>

    <div class="contact-list">
      <div>+1.555.010.246</div>
      <div>info@veltranomail.com</div>
      <div>www.veltranopolar.com</div>
    </div>
    <div class="divider"></div>
    <div class="address">
      <div>42 Glacier Point Road</div>
      <div>Ashford, VT 05401 USA</div>
    </div>
  </article>

  <article class="card card-back">
    <div class="back-lockup">
      <div class="back-mark"></div>
      <div class="back-text">
        <div class="brand-name">Veltrano.co</div>
        <div class="brand-tagline">Polar Expeditions Specialists</div>
      </div>
    </div>
  </article>
</body>
</html>
```